Vantro cards

I am in the auto motive, transportation business I would like a business card that is Something cool, modern edgy, having to do with car culture. I offer towing service for high and exotic cars. I also provide towing for collisions and car accidents. I offer open and enclosed transport nationwide.

Target Market(s)

Car culture people high end auto collectors

Industry/Entity Type

Towing car carrier

Contact Information for Business Card

My company colors black yellow and silver

Font styles to use
Serif

```html
<!DOCTYPE html>
<html lang="en">
<head>
<meta charset="utf-8">
<title>Vantro Transportation – Business Card</title>
<link href="https://fonts.googleapis.com/css2?family=Montserrat:wght@400;600;800&display=swap" rel="stylesheet">
<style>
  :root {
    --backdrop: #6e5843;
    --card-white: #ffffff;
    --ink: #1d1d1d;
    --brand-yellow: #f7d64a;
    --silver-light: #f4f4f4;
    --silver-mid: #c9c9c9;
    --silver-dark: #8d8d8d;
  }
  * { margin: 0; padding: 0; box-sizing: border-box; }
  html, body { width: 900px; height: 1200px; overflow: hidden; }
  body {
    background: var(--backdrop);
    font-family: "Montserrat", Arial, sans-serif;
    color: var(--ink);
  }
  .canvas { position: relative; width: 900px; height: 1200px; }

  .card {
    position: absolute;
    left: 80px;
    width: 742px;
    height: 441px;
    border-radius: 40px;
    overflow: hidden;
  }
  .card--front { top: 131px; background: var(--card-white); }
  .card--back {
    top: 637px;
    background:
      linear-gradient(115deg, transparent 30%, rgba(255,255,255,0.85) 42%, transparent 55%),
      linear-gradient(65deg, transparent 40%, rgba(255,255,255,0.7) 50%, transparent 62%),
      linear-gradient(160deg, var(--silver-mid) 0%, var(--silver-light) 35%, var(--silver-dark) 60%, var(--silver-light) 80%, var(--silver-mid) 100%);
  }

  .brand-name {
    position: absolute;
    display: flex;
    align-items: center;
    gap: 14px;
    font-weight: 800;
    color: var(--ink);
    text-transform: uppercase;
    line-height: 1.05;
  }
  .brand-mark { width: 22px; height: 22px; border-radius: 50%; background: var(--brand-yellow); flex: none; }
  .card--front .brand-name { left: 62px; top: 198px; font-size: 25px; }
  .card--back .brand-name { left: 0; right: 0; top: 188px; justify-content: center; font-size: 34px; }

  .divider {
    position: absolute;
    left: 346px; top: 126px;
    width: 2px; height: 213px;
    background: var(--brand-yellow);
  }

  .contact-block { position: absolute; left: 402px; top: 120px; }
  .person-name { font-size: 26px; font-weight: 600; color: var(--brand-yellow); line-height: 1.2; }
  .person-role { font-size: 16px; margin-top: 2px; }
  .contact-list { list-style: none; margin-top: 22px; font-size: 16.5px; }
  .contact-list li { display: flex; align-items: center; gap: 9px; height: 21px; }
  .contact-list svg { width: 13px; height: 13px; fill: var(--ink); flex: none; }
  .address { margin-top: 20px; font-size: 16.5px; line-height: 20px; }
</style>
</head>
<body>
<div class="canvas">

  <section class="card card--front">
    <div class="brand-name"><span class="brand-mark"></span><span>Vantro<br>Transportation</span></div>
    <div class="divider"></div>
    <div class="contact-block">
      <p class="person-name">Darren Cole</p>
      <p class="person-role">Owner</p>
      <ul class="contact-list">
        <li>
          <svg viewBox="0 0 16 16"><path d="M3 5c0-2 2-3 5-3s5 1 5 3v1h-3V5H6v1H3zM2 8h12v6H2zm4 1v2h4V9z"/></svg>
          <span>(555) 214-3390</span>
        </li>
        <li>
          <svg viewBox="0 0 16 16"><path d="M1 3h14v1L8 9 1 4zm0 3l7 5 7-5v7H1z"/></svg>
          <span>info@vantrotransportation.com</span>
        </li>
        <li>
          <svg viewBox="0 0 16 16"><path d="M8 1a7 7 0 1 0 0 14A7 7 0 0 0 8 1zm-1 2c-1 1-2 2-1 3s2 1 2 2-1 2 0 3 2 2 2 3a5.5 5.5 0 0 1-3-11zm3 1c1 1 3 2 3 4-1 0-2-1-3-1z"/></svg>
          <span>www.vantrotransportation.com</span>
        </li>
      </ul>
      <p class="address">48 Oak Ridge Road<br>Millbrook, PA 17020</p>
    </div>
  </section>

  <section class="card card--back">
    <div class="brand-name"><span class="brand-mark"></span><span>Vantro Transportation</span></div>
  </section>

</div>
</body>
</html>
```